Web Design job: SaaS start-up needs a cutting-edge web design

What's Needed:
- All designs files created
- Fully coded implementation in HTML/CSS/Bootstrap
- Pages: 5 -- see content here http://www.TeamVerdexa.com
-- Home Page
-- The Hidden Value
-- Benefits
-- About us
-- Careers
- The existing site has the textual content for each page. We can tweak to meet specific designs if needed.
- You will need to update/create image and interactive content for pages.

Reference:
Our existing website has a lot of content on it for reference -
http://www.TeamVerdexa.com

Description:
We need a web design that focuses in the UX and conveys the idea of magically fixing company problems by way of using our software.

Home Page
The main goal is to Drive Sales of the SaaS tool. When a visitor lands on our home page they should see: What we do, How we can help their problem and How to contact us.
1. Quickly understand What We Do
-- we sell SaaS software.
-- Need to quickly convey what our software does. It's seems complicated but really its not. See the description in about us for more info and visit our existing site.

2. How we can help their problem
-- We aim to solve any problem related to employees
-- Even if the visitor does not have a specific problem in mind, there are several areas organizations can always improve: (some examples below)
---- Create Stronger, More Productive Teams
---- Build Better Communications Pathways
---- Encourage Innovation and Positive Change
---- Develop and Retain Strong "Company Culture"

3. Be able to Contact Us to get started
-- contacting us to get a sales lead is the ultimate goal.
-- the user should not have to hunt to contact us. needs to be easy.

Other Pages (Hidden Value, Benefit, About Us, Careers):
-- These are informative pages about our software and process.
-- If we grab the attention of the user on the home page then these are the pages that they will explore for more info.
-- Should be able to link to these pages from the main nav or from sections with the homepage. For example: What We Do sections could link to the benefits page. How we help their problem sections could link to the Hidden Value page. Regardless of what links to where, the idea is that we will be able to nav to other areas.

About Us:
Our company name is TeamVerdexa (as in Organizational Analysis). We provide a software as a service (SaaS) that uses a simple 6-question survey to analyze the relationships of people within an Organization and provide leaders with ground-breaking Insights about their teams, interactive social network data visualizations to explore their team's composition and we give detailed profiles of the key players (i.e, who are the Social Bridges, Who are the Knowledge Bottlenecks, Who are the Best Mentors, Who are the people that are completely disconnected/out of the loop). Leaders then use this information to make high level organizational decisions.

What's unique about our software:
-- Powerful analysis results from just a 6-question "pulse-surveys"
-- Innovative Tools for visually exploring the organization through relationships as opposed to org-chart
-- Get real-time results as opposed to waiting months with traditional methods
-- Traditional Org-charts represent the organization's skeleton, whereas we uncover the organization's neural network (how it solves problems).

Preferred fonts (but could be convinced otherwise if looks great):
-- Section titles - Aleo
-- Main body - Lato
-- TeamVerdexa logo - Philosopher

Things we like:
-- We like a big slider as the top of the landing page.

Colors to include:
-- Colors in the logo (red, blue, green, teal) as accent colors

Feel of the site:
-- Cutting-edge Software
-- Professional
-- Social Network flare (we analyze relationships)

Note:
If we find a great match with a designer there is strong possibility to continue the relationship with follow on work redesigning our web-based application.

Target Market(s)

Current customers are Morrow Pike & Fenwell, Clearbrook Valley Bank.
We target anyone that manages a large team. Such as Corporate Leaders, High Level Managers, HR Leaders

Industry/Entity Type

Business Software

Contact Information for Business Card

Logo image
Name of company "TEAMVERDEXA" In Philosopher font.
Tagline: "Unlock the Hidden Value In Your Teams"
Person's Name, Title, email, phone.

Coding

Coded - Design and coding required

Number of Pages Required

4 page

Font styles to use
Other font styles liked:
• Lato, Philosopher, Aero

Colors
ec1f27
0255a3

Requirements
Must have
• See description.
Nice to have
• Things we like:
• We like a big slider as the top of the landing page. Ours is a little clunky and outdated but something fresh and sleek would be great.
• Colors to include:
• We would like to use the colors in the logo as accent colors in the site to give a consistent look and feel.
• Feel of the site:
• Cutting-edge Software
• Professional
• Social Network flare (we analyze relationships)

```html
<!DOCTYPE html>
<html lang="en">
<head>
<meta charset="utf-8">
<title>TeamVerdexa</title>
<link href="https://fonts.googleapis.com/css2?family=Aleo:wght@400;700&family=Lato:wght@400;700&family=Philosopher&display=swap" rel="stylesheet">
<style>
:root{
  --red:#e31e26;
  --blue:#1f57a6;
  --indigo:#3b4aa0;
  --green:#b8d43a;
  --teal:#7ed0ee;
  --ink:#222;
  --text:#555;
  --muted:#888;
  --soft:#f3f3f4;
  --rule:#ddd;
}
*{margin:0;padding:0;box-sizing:border-box}
html,body{width:776px;height:1200px;overflow:hidden;background:#fff}
body{position:relative;font-family:'Lato',sans-serif;color:var(--text)}
.abs{position:absolute}
.header{left:0;top:0;width:776px;height:66px;background:#fff}
.brand-tab{left:54px;top:-40px;width:136px;height:139px;border-radius:50%;background:#fff;border:2px solid var(--blue);border-top:none;z-index:5;display:flex;align-items:flex-end;justify-content:center;padding-bottom:28px;gap:5px}
.brand-tab .dot{width:10px;height:10px;border-radius:50%;background:var(--red)}
.brand-name{font-family:'Philosopher',sans-serif;color:var(--blue);font-size:14px;letter-spacing:.5px}
.contact-bar{top:13px;font-size:10px;color:var(--ink);display:flex;align-items:center;gap:6px}
.contact-bar b{font-weight:700}
.nav{top:40px;left:235px;display:flex;gap:27px;font-size:9.5px;color:var(--ink)}
.nav .active{color:var(--red)}
.hero{left:0;top:66px;width:776px;height:355px;background:linear-gradient(100deg,#c9ccd2 0%,#e9e4df 35%,#4a4e58 55%,#d9d3cc 75%,#3b3f47 100%)}
.hero-title{left:56px;top:230px;height:48px;padding:0 12px;background:var(--blue);color:#fff;font-family:'Aleo',serif;font-size:29px;line-height:48px}
.hero-sub{left:56px;top:278px;width:410px;height:32px;padding-left:8px;background:var(--red);color:#fff;font-size:14.5px;line-height:32px}
.arrow{top:256px;width:28px;height:28px;border-radius:50%;background:rgba(30,30,30,.75)}
.section-title{font-family:'Aleo',serif;font-weight:700;color:var(--ink)}
.what-title{top:459px;left:0;width:776px;text-align:center;font-size:20px}
.what-sub{top:490px;left:0;width:776px;text-align:center;font-size:8.5px}
.feature{width:170px;text-align:center}
.feature svg{display:block;margin:0 auto}
.feature h3{font-family:'Aleo',serif;font-weight:400;font-size:11px;color:var(--ink);margin-top:12px}
.feature p{font-size:7.5px;line-height:14.5px;margin-top:5px}
.help{left:0;top:716px;width:776px;height:276px;background:var(--soft)}
.help-title{left:56px;top:748px;font-size:19px}
.help-list{left:56px;top:788px;list-style:none;font-size:8.5px;color:#333;width:290px}
.help-list li{position:relative;padding-left:22px;line-height:14.5px;margin-bottom:14px}
.help-list li::before{content:"»";position:absolute;left:0;color:var(--red);font-weight:700}
.visual{left:364px;top:748px;width:380px;height:212px;border-radius:6px;background:radial-gradient(circle at 30% 40%,#f4c1d8,#d9d6f2 45%,#ffffff 80%)}
.footer-rule{left:0;top:992px;width:776px;height:2px;background:var(--red)}
.foot-brand{left:56px;top:1070px;display:flex;align-items:center;gap:6px}
.foot-brand .dot{width:12px;height:12px;border-radius:50%;background:var(--red)}
.foot-brand .brand-name{font-size:18px}
.foot-col h4{font-family:'Aleo',serif;font-weight:400;font-size:12px;color:var(--ink);letter-spacing:.3px;margin-bottom:10px}
.foot-col ul{list-style:none;font-size:7.5px;color:var(--muted)}
.foot-col li{height:20px;display:flex;align-items:center;gap:8px}
.bottom-rule{left:0;top:1164px;width:776px;height:1px;background:var(--rule)}
.copy{left:0;top:1176px;width:776px;text-align:center;font-size:7.5px;color:#444}
</style>
</head>
<body>
<header class="abs header"></header>
<div class="abs brand-tab"><span class="dot"></span><span class="brand-name">TEAMVERDEXA</span></div>
<div class="abs contact-bar" style="left:392px">
  <svg width="13" height="13" viewBox="0 0 13 13"><rect width="13" height="13" rx="2" fill="var(--blue)"/><path d="M4 3l1.5 2-1 1c.5 1 1.3 1.8 2.3 2.3l1-1 2 1.5-1 1.5C6 10 3.3 7.5 2.7 4z" fill="#fff"/></svg>
  <span>Call us on <b>555-214-0187</b></span>
</div>
<div class="abs contact-bar" style="left:534px">
  <svg width="13" height="13" viewBox="0 0 13 13"><rect width="13" height="13" rx="2" fill="var(--red)"/><rect x="3" y="4" width="7" height="5" fill="#fff"/><path d="M3 4l3.5 3L10 4" stroke="var(--red)" fill="none"/></svg>
  <span>Email us on <b>hello@teamverdexa.com</b></span>
</div>
<nav class="abs nav"><span class="active">HOME</span><span>ABOUT US</span><span>WHAT WE DO</span><span>HOW CAN WE HELP</span><span>WHAT'S UNIQUE</span><span>CONTACT US</span></nav>

<section class="abs hero" role="img" aria-label="Photo of business people smiling in a meeting"></section>
<div class="abs hero-title">TEAMVERDEXA</div>
<div class="abs hero-sub">Powerful analysis results from just a 6-question "pulse-surveys"</div>
<svg class="abs arrow" style="left:16px" viewBox="0 0 28 28"><path d="M16 8l-6 6 6 6" stroke="#fff" stroke-width="2.5" fill="none"/></svg>
<svg class="abs arrow" style="left:727px" viewBox="0 0 28 28"><path d="M12 8l6 6-6 6" stroke="#fff" stroke-width="2.5" fill="none"/></svg>

<h2 class="abs section-title what-title">WHAT WE DO</h2>
<p class="abs what-sub">We sell SaaS software. Need to quickly convey what our software does. It's seems complicated but really its not.</p>

<div class="abs feature" style="left:39px;top:525px">
  <svg width="94" height="94" viewBox="0 0 94 94"><circle cx="47" cy="47" r="46" fill="#fff" stroke="var(--green)" stroke-width="1.5"/><circle cx="47" cy="47" r="42" fill="var(--green)"/><rect x="24" y="33" width="12" height="26" rx="1" fill="none" stroke="#fff" stroke-width="2.5"/><rect x="40" y="31" width="30" height="21" rx="1" fill="none" stroke="#fff" stroke-width="2.5"/><path d="M50 59h10M55 52v7" stroke="#fff" stroke-width="2.5"/></svg>
  <h3>Online Pulse Survey</h3>
  <p>Our company name is TeamVerdexa (as<br>in Organizational Analysis).</p>
</div>
<div class="abs feature" style="left:215px;top:525px">
  <svg width="94" height="94" viewBox="0 0 94 94"><circle cx="47" cy="47" r="46" fill="#fff" stroke="var(--indigo)" stroke-width="1.5"/><circle cx="47" cy="47" r="42" fill="var(--indigo)"/><circle cx="47" cy="45" r="9" fill="none" stroke="#fff" stroke-width="2.5" stroke-dasharray="3 2.2"/><circle cx="47" cy="45" r="3.5" fill="none" stroke="#fff" stroke-width="2"/></svg>
  <h3>Proprietary Algorithms</h3>
  <p>Our company name is TeamVerdexa (as<br>in Organizational Analysis).</p>
</div>
<div class="abs feature" style="left:390px;top:525px">
  <svg width="94" height="94" viewBox="0 0 94 94"><circle cx="47" cy="47" r="46" fill="#fff" stroke="var(--teal)" stroke-width="1.5"/><circle cx="47" cy="47" r="42" fill="var(--teal)"/><path d="M28 34h10a4 4 0 118 0h10v10a4 4 0 110 8v10H46a4 4 0 10-8 0H28V52a4 4 0 100-8z" fill="#fff"/></svg>
  <h3>Organizational Key Insights</h3>
  <p>Our company name is TeamVerdexa (as<br>in Organizational Analysis).</p>
</div>
<div class="abs feature" style="left:565px;top:525px">
  <svg width="94" height="94" viewBox="0 0 94 94"><circle cx="47" cy="47" r="46" fill="#fff" stroke="var(--red)" stroke-width="1.5"/><circle cx="47" cy="47" r="42" fill="var(--red)"/><path d="M24 42l8-6 9 3 6-3 6 3 9-3 8 6-7 8-10 8-6-5-6 5-10-8z" fill="#fff"/></svg>
  <h3>Expert Review &amp; Action Plans</h3>
  <p>Our company name is TeamVerdexa (as<br>in Organizational Analysis).</p>
</div>

<section class="abs help"></section>
<h2 class="abs section-title help-title">HOW WE CAN HELP</h2>
<ul class="abs help-list">
  <li>We aim to solve any problem related to employees</li>
  <li>Create Stronger, More Productive Teams</li>
  <li>Build Better Communications Pathways</li>
  <li>Encourage Innovation and Positive Change</li>
  <li>Develop and Retain Strong "Company Culture"</li>
  <li>Even if the visitor does not have a specific problem in mind, there are several areas organizations can always improve</li>
</ul>
<div class="abs visual" role="img" aria-label="Desktop and browser screens showing colorful social network visualizations"></div>

<div class="abs footer-rule"></div>
<div class="abs foot-brand"><span class="dot"></span><span class="brand-name">TEAMVERDEXA</span></div>

<div class="abs foot-col" style="left:234px;top:1018px">
  <h4>CONTACT US</h4>
  <ul>
    <li><svg width="7" height="9" viewBox="0 0 7 9"><path d="M3.5 9C1 5.5 0 4.5 0 3.5a3.5 3.5 0 017 0C7 4.5 6 5.5 3.5 9z" fill="var(--red)"/><circle cx="3.5" cy="3.5" r="1.2" fill="#fff"/></svg>Springfield, OH</li>
    <li><svg width="8" height="8" viewBox="0 0 13 13"><path d="M2 1l3 3-1.5 1.5c1 2 2 3 4 4L9 8l3 3-2 2C5 12 1 8 0 3z" fill="var(--red)"/></svg>Phone - 555-214-0187</li>
    <li><svg width="8" height="8" viewBox="0 0 8 8"><rect y="2" width="8" height="6" fill="var(--red)"/><rect x="2" width="4" height="3" fill="var(--red)"/></svg>Fax - (555) 390-4471</li>
    <li><svg width="9" height="7" viewBox="0 0 9 7"><rect x=".5" y=".5" width="8" height="6" fill="none" stroke="var(--red)"/><path d="M.5.5l4 3 4-3" stroke="var(--red)" fill="none"/></svg>E-mail - hello@teamverdexa.com</li>
  </ul>
</div>
<div class="abs foot-col" style="left:402px;top:1018px">
  <h4>QUICK LINKS</h4>
  <ul><li>Products</li><li>Support</li><li>Where to buy</li><li>Register your Warranty</li><li>About</li></ul>
</div>
<div class="abs foot-col" style="left:530px;top:1018px">
  <h4>OUR POLICY</h4>
  <ul><li>Help &amp; Contact</li><li>Policy</li><li>Affiliates</li><li>Guidelines</li></ul>
</div>
<div class="abs foot-col" style="left:646px;top:1019px">
  <h4>COMMUNITY</h4>
  <ul><li>Terms &amp; conditions</li><li>privacy policy</li><li>site map</li><li>Contact us</li></ul>
</div>

<div class="abs bottom-rule"></div>
<p class="abs copy">Copyright ©2016 Company Name. All rights reserved.</p>
</body>
</html>
```